Business Card & Letterhead Design

We a financial advice company based in Australia. We provide advice to wealthy farmers.

We are changing our business name FROM Brightvale Financial TO Tallowmere Wealth and we need a new letterhead and double sided business card design

Attached is designs from our previous branding (Brightvale Financial) as it includes all the details we require on the new Tallowmere Wealth business cards and letterhead.

Need extra days to review

```html
<!DOCTYPE html>
<html lang="en">
<head>
<meta charset="utf-8">
<title>Tallowmere Wealth – Business Card</title>
<link rel="stylesheet" href="https://fonts.googleapis.com/css2?family=Source+Sans+3:wght@400&display=swap">
<style>
  :root {
    --page: #ffffff;
    --slate: #5f6b72;
    --panel: #ffffff;
    --ink-light: #ffffff;
    --shadow: rgba(30, 36, 40, 0.55);
  }
  * { margin: 0; padding: 0; box-sizing: border-box; }
  html, body {
    width: 1200px;
    height: 1000px;
    overflow: hidden;
    background: var(--page);
  }
  body {
    position: relative;
    font-family: "Source Sans 3", "Myriad Pro", sans-serif;
    font-weight: 400;
  }
  .card {
    position: absolute;
    left: 68px;
    top: 205px;
    width: 1061px;
    height: 590px;
    background: var(--slate);
  }
  .brand-panel {
    position: absolute;
    left: 80px;
    top: 59px;
    width: 419px;
    height: 472px;
    background: var(--panel);
    box-shadow: 10px 10px 12px var(--shadow);
    color: var(--slate);
    text-align: center;
  }
  .brand-name {
    position: absolute;
    left: 0;
    right: 0;
    top: 90px;
    font-size: 40px;
    line-height: 1.1;
    letter-spacing: 0.5px;
  }
  .services {
    position: absolute;
    left: 0;
    right: 0;
    top: 235px;
    list-style: none;
    font-size: 38px;
    line-height: 58px;
  }
  .details {
    position: absolute;
    left: 564px;
    top: 103px;
    color: var(--ink-light);
    font-size: 31px;
    line-height: 40px;
  }
  .details p + p { margin-top: 48px; }
</style>
</head>
<body>
  <section class="card" aria-label="Tallowmere Wealth business card">
    <div class="brand-panel">
      <div class="brand-name">Tallowmere<br>Wealth</div>
      <ul class="services">
        <li>Life &amp; TPD Insurance</li>
        <li>Income Protection</li>
        <li>Financial Planning</li>
        <li>Retirement Planning</li>
      </ul>
    </div>
    <div class="details">
      <p class="address">
        Suite 14C, 38 Weyland St<br>
        Riverbend Point QLD 4172<br>
        PO Box 5318<br>
        East Marlowe QLD 4172
      </p>
      <p class="licensee">
        Kestrel Financial Planning<br>
        Limited<br>
        Australian Financial Services<br>
        Licensee<br>
        License Number 418273
      </p>
    </div>
  </section>
</body>
</html>
```